Business Card Design Project - 2 sided

We need a business card design for a card having one business on each side (ie. two businesses on one card). Would like a design that incorporates logo, tagline and normal fields (name, position, address, phone).

Would also like an allowance for small font text along the bottom (text to be determined, but less than 50 characters).

NB. Attached logo for Harbor Quill has two variations - either can be used.

www.harborquill-example.com / www.velmaro-example.com

```html
<!DOCTYPE html>
<html lang="en">
<head>
<meta charset="utf-8">
<title>Two-sided business card</title>
<link rel="stylesheet" href="https://fonts.googleapis.com/css2?family=Open+Sans:wght@400;600;700&display=swap">
<style>
  :root {
    --backdrop: #4a2a18;
    --card-white: #ffffff;
    --navy: #2a2566;
    --lime: #8cc63f;
    --sky: #3a8fcf;
    --leaf-dark: #6f9e33;
    --leaf-light: #a6cf58;
    --ink-grey: #3d3d3d;
    --text-light: #ffffff;
  }
  * { margin: 0; padding: 0; box-sizing: border-box; }
  html, body { width: 1200px; height: 412px; overflow: hidden; }
  body {
    background: var(--backdrop);
    font-family: "Open Sans", Arial, sans-serif;
    position: relative;
  }
  .card {
    position: absolute;
    top: 64px;
    width: 498px;
    height: 284px;
    background: var(--card-white);
    overflow: hidden;
    box-shadow: 0 4px 10px rgba(0,0,0,0.45);
  }
  .card--harbor { left: 74px; }
  .card--velmaro { left: 629px; }
  .card__waves { position: absolute; inset: 0; width: 498px; height: 284px; }

  .brand {
    position: absolute;
    display: flex;
    align-items: center;
    gap: 8px;
    font-weight: 600;
    white-space: nowrap;
  }
  .brand__dot { border-radius: 50%; display: block; }
  .card--harbor .brand { left: 34px; top: 90px; font-size: 21px; color: var(--navy); letter-spacing: 1px; }
  .card--harbor .brand__dot { width: 18px; height: 18px; background: var(--lime); }
  .card--velmaro .brand { left: 30px; top: 44px; font-size: 40px; color: var(--sky); }
  .card--velmaro .brand__dot { width: 36px; height: 36px; background: var(--lime); }

  .tagline { position: absolute; white-space: nowrap; }
  .card--harbor .tagline { left: 24px; top: 124px; font-size: 9.5px; font-weight: 600; color: #222; }
  .card--velmaro .tagline { left: 68px; top: 96px; font-size: 13px; font-weight: 700; color: var(--ink-grey); }

  .person { position: absolute; left: 24px; top: 168px; font-size: 15px; font-weight: 700; white-space: nowrap; }
  .person__title { font-size: 12px; font-weight: 400; }
  .card--harbor .person { color: var(--navy); }
  .card--velmaro .person { left: 36px; color: var(--sky); }

  .contact {
    position: absolute;
    right: 20px;
    top: 148px;
    list-style: none;
    color: var(--text-light);
    font-size: 12px;
    line-height: 16.5px;
    text-align: right;
  }
  .contact li { display: flex; justify-content: flex-end; align-items: center; gap: 6px; }
  .contact svg { width: 10px; height: 10px; fill: var(--text-light); }
  .address { position: absolute; left: 199px; top: 245px; font-size: 12px; color: var(--text-light); white-space: nowrap; }
  .fine-print { position: absolute; left: 160px; top: 267px; font-size: 9px; color: var(--text-light); white-space: nowrap; letter-spacing: 0.2px; }
</style>
</head>
<body>

<section class="card card--harbor" aria-label="Harbor Quill side">
  <svg class="card__waves" viewBox="0 0 498 284" aria-hidden="true">
    <path fill="var(--lime)" d="M0,205 C80,214 170,222 260,165 C340,114 420,92 498,88 L498,104 C420,108 350,128 275,176 C180,236 80,236 0,226 Z"/>
    <path fill="var(--navy)" d="M0,240 C90,250 190,245 270,192 C350,140 420,118 498,114 L498,284 L0,284 Z"/>
    <path fill="none" stroke="var(--navy)" stroke-width="2" d="M60,234 C160,240 220,224 278,180 C350,128 430,110 498,107"/>
    <path fill="none" stroke="#ffffff" stroke-width="1.2" d="M30,262 C150,282 260,258 350,200"/>
  </svg>
  <div class="brand"><span class="brand__dot"></span>HARBOR QUILL</div>
  <p class="tagline">Website Translation and Localisation Specialist...</p>
  <p class="person">Your Name <span class="person__title">/ Title</span></p>
  <ul class="contact">
    <li>123-456-7890 <svg viewBox="0 0 10 10"><path d="M2 0h2l1 3-1.5 1a6 6 0 0 0 2.5 2.5L7 5l3 1v2c0 1-1 2-2 2A8 8 0 0 1 0 2c0-1 1-2 2-2z"/></svg></li>
    <li>123-456-7890 <svg viewBox="0 0 10 10"><path d="M2.5 0h5v10h-5z M3.5 1v6h3V1z"/></svg></li>
    <li>123-456-7890 <svg viewBox="0 0 10 10"><path d="M2 0h6v3h2v6H0V3h2z M3 1v2h4V1z M2 6v2h6V6z"/></svg></li>
    <li>name@website.com <svg viewBox="0 0 10 10"><path d="M0 2h10v6H0z M1 3l4 3 4-3z"/></svg></li>
    <li>www.website.com <svg viewBox="0 0 10 10"><circle cx="5" cy="5" r="5"/></svg></li>
  </ul>
  <p class="address">Complex name, Street name, City, State, zip code</p>
  <p class="fine-print">xxxxxxxxxxxxxxxxxxxxxxxxxxxxxxxxxxxxxxxxxxxxxxxxxxx</p>
</section>

<section class="card card--velmaro" aria-label="Velmaro side">
  <svg class="card__waves" viewBox="0 0 498 284" aria-hidden="true">
    <defs>
      <radialGradient id="leafGlow" cx="0.55" cy="0.35" r="0.8">
        <stop offset="0" stop-color="var(--leaf-light)"/>
        <stop offset="1" stop-color="var(--leaf-dark)"/>
      </radialGradient>
    </defs>
    <path fill="var(--sky)" d="M0,205 C80,214 170,222 260,165 C340,114 420,92 498,88 L498,104 C420,108 350,128 275,176 C180,236 80,236 0,226 Z"/>
    <path fill="url(#leafGlow)" d="M0,240 C90,250 190,245 270,192 C350,140 420,118 498,114 L498,284 L0,284 Z"/>
    <path fill="none" stroke="#ffffff" stroke-width="1.2" d="M30,262 C150,282 260,258 350,200"/>
  </svg>
  <div class="brand"><span class="brand__dot"></span>Velmaro</div>
  <p class="tagline">Professional SEO Services</p>
  <p class="person">Your Name <span class="person__title">/ Title</span></p>
  <ul class="contact">
    <li>123-456-7890 <svg viewBox="0 0 10 10"><path d="M2 0h2l1 3-1.5 1a6 6 0 0 0 2.5 2.5L7 5l3 1v2c0 1-1 2-2 2A8 8 0 0 1 0 2c0-1 1-2 2-2z"/></svg></li>
    <li>123-456-7890 <svg viewBox="0 0 10 10"><path d="M2.5 0h5v10h-5z M3.5 1v6h3V1z"/></svg></li>
    <li>123-456-7890 <svg viewBox="0 0 10 10"><path d="M2 0h6v3h2v6H0V3h2z M3 1v2h4V1z M2 6v2h6V6z"/></svg></li>
    <li>name@website.com <svg viewBox="0 0 10 10"><path d="M0 2h10v6H0z M1 3l4 3 4-3z"/></svg></li>
    <li>www.website.com <svg viewBox="0 0 10 10"><circle cx="5" cy="5" r="5"/></svg></li>
  </ul>
  <p class="address">Complex name, Street name, City, State, zip code</p>
  <p class="fine-print">xxxxxxxxxxxxxxxxxxxxxxxxxxxxxxxxxxxxxxxxxxxxxxxxxxx</p>
</section>

</body>
</html>
```